Business Cards Needed for Innovative Healthcare Marketing Company

We are a marketing company focused on healthcare. Our company is all about rebranding yourself renewing your image and generating results. The phoenix stands for "reborn" or "rising" which we provide new brands for our clients we take their old brands and renew it with creativity and innovation. I am looking for a business card with color dimension. I have attached an example of a card I think has the look and feel of what I am trying to accomplish. I like that the card example has black and grey font colors, I like the font placement and the small logo, I really like the use of the colors on the right those are the colors of my logo. My logo is phoenix so maybe incorporating flames similar to that design. I would like the back a solid color maybe red with an opaque version of the logo and website. As a marketing company I am always open to creative liberty!

Target Market(s)

Doctors and business professionals.

Industry/Entity Type

Marketing

Contact Information for Business Card

Valcorne Health Care Marketing
Marla Tenwick- CEO
#(512)638-2974
email-marla@valcorne.com
website- valcorne.com

Font styles to use
Sans Serif

Colors
ec1f27
f37122
ffc214
fbed22
fbf289
f04a50

Requirements
Must have
• The logo and required information
Nice to have
• icons by the information
Should not have
• child like font

```html
<!DOCTYPE html>
<html lang="en">
<head>
<meta charset="utf-8">
<title>Valcorne Health Care Marketing – Business Cards</title>
<link rel="stylesheet" href="https://fonts.googleapis.com/css2?family=Montserrat:wght@300;400;600&display=swap">
<style>
  :root {
    --backdrop: #2b2b2c;
    --card: #050505;
    --white: #f4f4f4;
    --grey: #b9b9b9;
    --rule: #5a2a26;
    --orange: #f7a21b;
    --flame-red: #d9452a;
    --flame-orange: #f37122;
    --flame-gold: #f7a21b;
  }
  * { box-sizing: border-box; margin: 0; padding: 0; }
  html, body { width: 1200px; height: 900px; overflow: hidden; }
  body {
    background: var(--backdrop);
    font-family: "Montserrat", sans-serif;
    color: var(--white);
    display: flex;
    flex-direction: column;
    align-items: center;
    justify-content: center;
    gap: 20px;
  }
  .card {
    position: relative;
    width: 740px;
    height: 423px;
    background: var(--card);
    border-radius: 22px;
    box-shadow: 0 10px 30px rgba(0,0,0,.45);
    overflow: hidden;
  }

  /* Back */
  .card--back .brand-lockup {
    position: absolute;
    left: 50%;
    top: 150px;
    transform: translateX(-50%);
    display: flex;
    align-items: center;
    gap: 18px;
  }
  .brand-dot {
    width: 64px; height: 64px;
    border-radius: 50%;
    background: var(--flame-orange);
    flex: none;
  }
  .wordmark {
    font-weight: 300;
    letter-spacing: 3px;
    line-height: 1;
    color: var(--white);
  }
  .card--back .wordmark { font-size: 48px; }
  .tagline {
    font-weight: 300;
    letter-spacing: 1.5px;
    color: var(--grey);
    border-top: 1px solid var(--rule);
    margin-top: 6px;
    padding-top: 6px;
  }
  .card--back .tagline { font-size: 17px; }
  .card--back .website {
    position: absolute;
    left: 0; right: 0;
    bottom: 58px;
    text-align: center;
    font-size: 20px;
    font-weight: 400;
    letter-spacing: .5px;
  }

  /* Front */
  .card--front .details {
    position: absolute;
    left: 60px;
    top: 120px;
  }
  .card--front .wordmark { font-size: 52px; }
  .card--front .tagline { font-size: 17px; }
  .person-name {
    margin-top: 18px;
    font-size: 23px;
    font-weight: 600;
    color: var(--orange);
    letter-spacing: 1px;
  }
  .person-title {
    font-size: 16px;
    font-weight: 400;
    color: var(--white);
    margin-bottom: 14px;
  }
  .contact-list { list-style: none; }
  .contact-list li {
    display: flex;
    align-items: center;
    gap: 10px;
    font-size: 17px;
    line-height: 25px;
  }
  .contact-list svg { width: 13px; height: 13px; fill: var(--orange); flex: none; }
  .emblem-area {
    position: absolute;
    right: 70px;
    top: 50px;
    width: 270px;
    height: 270px;
    border-radius: 50%;
    background: var(--flame-orange);
  }
</style>
</head>
<body>

  <section class="card card--back">
    <div class="brand-lockup">
      <span class="brand-dot"></span>
      <div>
        <div class="wordmark">VALCORNE</div>
        <div class="tagline">HEALTHCARE MARKETING</div>
      </div>
    </div>
    <div class="website">www.valcorne.com</div>
  </section>

  <section class="card card--front">
    <div class="details">
      <div class="wordmark">VALCORNE</div>
      <div class="tagline">HEALTHCARE MARKETING</div>
      <div class="person-name">MARLA TENWICK</div>
      <div class="person-title">CEO</div>
      <ul class="contact-list">
        <li>
          <svg viewBox="0 0 24 24" aria-hidden="true"><path d="M6.6 10.8a15.1 15.1 0 0 0 6.6 6.6l2.2-2.2a1 1 0 0 1 1-.25 11.4 11.4 0 0 0 3.6.57 1 1 0 0 1 1 1V20a1 1 0 0 1-1 1A17 17 0 0 1 3 4a1 1 0 0 1 1-1h3.5a1 1 0 0 1 1 1c0 1.25.2 2.45.57 3.57a1 1 0 0 1-.25 1z"/></svg>
          (512)638-2974
        </li>
        <li>
          <svg viewBox="0 0 24 24" aria-hidden="true"><path d="M2 5h20v14H2zm2 2v.5l8 5 8-5V7zm0 2.9V17h16V9.9l-8 5z"/></svg>
          marla@valcorne.com
        </li>
        <li>
          <svg viewBox="0 0 24 24" aria-hidden="true"><path d="M12 2a10 10 0 1 0 0 20 10 10 0 0 0 0-20zm6.9 6h-3a15 15 0 0 0-1.3-3.9A8 8 0 0 1 18.9 8zM12 4c.8 1.1 1.5 2.5 1.9 4h-3.8c.4-1.5 1.1-2.9 1.9-4zM4.3 14a8 8 0 0 1 0-4h3.4a16 16 0 0 0 0 4zm.8 2h3a15 15 0 0 0 1.3 3.9A8 8 0 0 1 5.1 16zm3-8h-3a8 8 0 0 1 4.3-3.9A15 15 0 0 0 8.1 8zM12 20c-.8-1.1-1.5-2.5-1.9-4h3.8c-.4 1.5-1.1 2.9-1.9 4zm2.3-6H9.7a14 14 0 0 1 0-4h4.6a14 14 0 0 1 0 4zm.3 5.9a15 15 0 0 0 1.3-3.9h3a8 8 0 0 1-4.3 3.9zm1.7-5.9a16 16 0 0 0 0-4h3.4a8 8 0 0 1 0 4z"/></svg>
          www.valcorne.com
        </li>
      </ul>
    </div>
    <div class="emblem-area" role="img" aria-label="Large brand emblem area in red-orange flame tones"></div>
  </section>

</body>
</html>
```